Hollow Thicket, a 3d voxel survival video game needs a card for gaming conventions

I am the lead developer for Hollow Thicket http://www.HollowThicket.example and need a business card to hand out at an indie gaming convention
The card would need to include the game name, website url, my name, position (Lead Developer), e-mail and phone number
The game is a 3d, voxel (with smooth terrain) based survival game with guns and wildlife. The main icon of the game would likely be a grizzly bear but I am willing to accept other designs too.
Attached is a media kit for the game with some images you can use but don't have to its just what little art I can provide. Anything on the website or from the video game can also be used. unrelated art can also be used.
Target Market(s)
Indie Developers/publishers at conferences
Industry/Entity Type
Games
Contact Information for Business Card
Name: Corin Waldrick
Position: Lead Developer
E-mail: Pale_Kettle@mailbox.example
Phone number: 555-372-1186

```html
<!DOCTYPE html>
<html lang="en">
<head>
<meta charset="utf-8">
<title>Hollow Thicket — Business Card</title>
<link rel="stylesheet" href="https://fonts.googleapis.com/css2?family=PT+Sans:wght@400;700&display=swap">
<style>
  :root {
    --page: #d9d6d2;
    --card: #0b0b0b;
    --logo: #c9b27a;
    --name: #d8622e;
    --text: #e9e9e9;
    --icon: #d8622e;
    --fur-light: #8a6a4a;
    --fur-dark: #3b2a1c;
  }
  html, body {
    margin: 0;
    width: 1200px;
    height: 844px;
    overflow: hidden;
    background: var(--page);
    font-family: "PT Sans", sans-serif;
  }
  .sheet {
    width: 1200px;
    height: 844px;
    display: flex;
    align-items: center;
    justify-content: center;
    gap: 40px;
  }
  .card {
    position: relative;
    width: 540px;
    height: 309px;
    background: var(--card);
    overflow: hidden;
    box-shadow: 0 6px 18px rgba(0,0,0,.25);
  }
  .wordmark {
    margin: 0;
    color: var(--logo);
    font-weight: 700;
    text-transform: uppercase;
    letter-spacing: 3px;
    line-height: 1;
  }
  .card-front .wordmark {
    position: absolute;
    left: 38px;
    top: 78px;
    font-size: 34px;
  }
  .wordmark span { display: block; }
  .wordmark .line-two { padding-left: 34px; }
  .bear-photo {
    position: absolute;
    right: 0;
    top: 58px;
    width: 270px;
    height: 251px;
    background: radial-gradient(ellipse at 45% 55%, var(--fur-light) 0%, var(--fur-dark) 70%, var(--card) 100%);
    border-top-left-radius: 120px 90px;
  }
  .contact {
    position: absolute;
    left: 38px;
    top: 170px;
    color: var(--text);
  }
  .contact-name {
    margin: 0;
    color: var(--name);
    font-size: 17px;
    font-weight: 700;
    line-height: 1.2;
  }
  .contact-role {
    margin: 2px 0 16px;
    font-size: 13px;
    line-height: 1.2;
  }
  .contact-line {
    display: flex;
    align-items: center;
    gap: 8px;
    margin: 0 0 5px;
    font-size: 13px;
    line-height: 17px;
    white-space: nowrap;
  }
  .contact-line svg { width: 11px; height: 11px; fill: var(--icon); flex: none; }
  .contact-line .icon-web { fill: none; stroke: var(--icon); stroke-width: 2; }
  .card-back {
    display: flex;
    align-items: center;
    justify-content: center;
  }
  .card-back .wordmark { font-size: 44px; }
  .card-back .wordmark .line-two { padding-left: 44px; }
</style>
</head>
<body>
<main class="sheet">
  <section class="card card-front" aria-label="Card front">
    <h1 class="wordmark"><span>Hollow</span><span class="line-two">Thicket</span></h1>
    <div class="bear-photo" role="img" aria-label="Photo of a roaring grizzly bear"></div>
    <div class="contact">
      <p class="contact-name">Corin Waldrick</p>
      <p class="contact-role">Lead Developer</p>
      <p class="contact-line">
        <svg viewBox="0 0 24 24" aria-hidden="true"><path d="M6.6 10.8a15.1 15.1 0 0 0 6.6 6.6l2.2-2.2a1 1 0 0 1 1-.25 11.4 11.4 0 0 0 3.6.57 1 1 0 0 1 1 1V20a1 1 0 0 1-1 1A17 17 0 0 1 3 4a1 1 0 0 1 1-1h3.5a1 1 0 0 1 1 1c0 1.25.2 2.45.57 3.6a1 1 0 0 1-.25 1z"/></svg>
        555-372-1186
      </p>
      <p class="contact-line">
        <svg viewBox="0 0 24 24" aria-hidden="true"><path d="M2 5h20v14H2z M3 6l9 7 9-7" /></svg>
        Pale_Kettle@mailbox.example
      </p>
      <p class="contact-line">
        <svg class="icon-web" viewBox="0 0 24 24" aria-hidden="true"><circle cx="12" cy="12" r="10"/><path d="M2 12h20M12 2c3 3 3 17 0 20M12 2c-3 3-3 17 0 20"/></svg>
        www.HollowThicket.example
      </p>
    </div>
  </section>
  <section class="card card-back" aria-label="Card back">
    <h2 class="wordmark"><span>Hollow</span><span class="line-two">Thicket</span></h2>
  </section>
</main>
</body>
</html>
```